Form With Marla - Health and Wellness Business Card and Logo

I need a business card design with a logo for my business you can check out at www.formwithmarla.net. I want something more original, simplistic, and memorable than the basic logo I have on my site currently. I am a health and wellness coach and I offer mindset coaching and nutrition plans. I like the colour teal and dark grey/black for my theme colours. I emphasize growth, longterm change, and the whole package of "healthy mind, healthy body, healthy life". I had played around the idea of intertwining 3 M's or incorporating growth (leaves etc.) into my design. I want my expertise and experience to show through. In one glance I want people to understand with confidence I can help them accomplish anything they set their minds to. I look forward to seeing what everyone comes up with!

Industry/Entity Type

Health And Wellness

Contact Information for Business Card

Form With Marla
Marla Prentiss
BSc, Health & Wellness Coach
"Manifest your best"
www.formwithmarla.net
formwithmarla@quillpost.net
472-618-9043

Colors
33b8a4
ffffff
333333
000000

Requirements
Must have
• A memorable and unique logo for my business!
Nice to have
• Could have the phrase "Are you unhappy with your body and state of health?" or "It takes the right skills to develop habits in order to create long term change. I can help you get there."

```html
<!DOCTYPE html>
<html lang="en">
<head>
<meta charset="utf-8">
<title>Form With Marla — Business Card</title>
<link rel="stylesheet" href="https://fonts.googleapis.com/css2?family=Questrial&family=Open+Sans:wght@400;700&display=swap">
<style>
  :root {
    --stage: #2b2b2b;
    --card-dark: #141414;
    --card-light: #ffffff;
    --ink: #000000;
    --ink-soft: #333333;
    --emboss: #6a6a6a;
    --teal: #33b8a4;
  }
  * { margin: 0; padding: 0; box-sizing: border-box; }
  html, body {
    width: 1200px;
    height: 900px;
    overflow: hidden;
    background: var(--stage);
  }
  .canvas { position: relative; width: 1200px; height: 900px; }
  .card { position: absolute; left: 280px; width: 640px; height: 366px; }

  .card--back {
    top: 58px;
    background: var(--card-dark);
    display: flex;
    flex-direction: column;
    align-items: center;
    justify-content: center;
    gap: 14px;
  }
  .back__mark {
    display: flex;
    align-items: center;
    gap: 14px;
    font-family: "Questrial", sans-serif;
    font-size: 36px;
    color: var(--emboss);
    letter-spacing: 0.5px;
    padding-bottom: 8px;
    border-bottom: 1px solid var(--emboss);
  }
  .back__square { width: 24px; height: 24px; background: var(--teal); }
  .back__tagline {
    font-family: "Questrial", sans-serif;
    font-size: 16px;
    letter-spacing: 2px;
    color: var(--teal);
  }

  .card--front { top: 476px; background: var(--card-light); }
  .front__title {
    position: absolute;
    left: 40px;
    top: 24px;
    font-family: "Questrial", sans-serif;
    font-weight: 400;
    font-size: 44px;
    color: var(--ink-soft);
    letter-spacing: 0.5px;
  }
  .front__tab {
    position: absolute;
    left: 0;
    top: 112px;
    width: 10px;
    height: 40px;
    background: var(--teal);
    border-radius: 0 4px 4px 0;
  }
  .person {
    position: absolute;
    left: 40px;
    top: 108px;
    font-family: "Open Sans", sans-serif;
    color: var(--ink);
  }
  .person__name { font-size: 30px; font-weight: 700; letter-spacing: 0.5px; line-height: 1.15; }
  .person__role { font-size: 14px; font-weight: 700; margin-top: 2px; color: var(--ink-soft); }
  .person__tagline {
    font-family: "Questrial", sans-serif;
    font-size: 14px;
    color: var(--teal);
    margin-top: 6px;
    letter-spacing: 0.5px;
  }
  .contacts {
    position: absolute;
    left: 40px;
    top: 226px;
    list-style: none;
    font-family: "Open Sans", sans-serif;
    font-size: 15px;
    color: var(--ink-soft);
    letter-spacing: 0.6px;
  }
  .contacts li { display: flex; align-items: center; gap: 12px; height: 26px; }
  .contacts svg { width: 14px; height: 14px; flex: none; }
  .front__mark {
    position: absolute;
    right: 36px;
    bottom: 40px;
    display: flex;
    align-items: center;
    gap: 12px;
    font-family: "Questrial", sans-serif;
    font-size: 22px;
    color: var(--ink-soft);
  }
  .front__square { width: 22px; height: 22px; background: var(--teal); }
</style>
</head>
<body>
<main class="canvas">
  <section class="card card--back" aria-label="Card back">
    <div class="back__mark">
      <span class="back__square"></span>
      <span>form with marla</span>
    </div>
    <p class="back__tagline">MANIFEST YOUR BEST</p>
  </section>

  <section class="card card--front" aria-label="Card front">
    <h1 class="front__title">form with marla</h1>
    <span class="front__tab"></span>
    <div class="person">
      <p class="person__name">MARLA PRENTISS</p>
      <p class="person__role">BSc, Health &amp; Wellness Coach</p>
      <p class="person__tagline">"Manifest your best"</p>
    </div>
    <ul class="contacts">
      <li>
        <svg viewBox="0 0 14 14" aria-hidden="true"><path d="M3.5 1.5 L5.5 1.5 L6.5 4.5 L5 5.8 Q6.2 8.2 8.2 9 L9.5 7.5 L12.5 8.5 L12.5 10.5 Q12 12.5 10 12.5 Q2 11.5 1.5 4 Q1.5 2 3.5 1.5 Z" fill="#33b8a4"/></svg>
        472-618-9043
      </li>
      <li>
        <svg viewBox="0 0 14 14" aria-hidden="true"><rect x="1" y="3" width="12" height="8" fill="#33b8a4"/><path d="M1 3 L7 8 L13 3" stroke="#fff" stroke-width="1.2" fill="none"/></svg>
        formwithmarla@quillpost.net
      </li>
      <li>
        <svg viewBox="0 0 14 14" aria-hidden="true"><circle cx="7" cy="7" r="6" fill="none" stroke="#33b8a4" stroke-width="1.4"/><ellipse cx="7" cy="7" rx="2.5" ry="6" fill="none" stroke="#33b8a4" stroke-width="1.2"/><line x1="1" y1="7" x2="13" y2="7" stroke="#33b8a4" stroke-width="1.2"/></svg>
        www.formwithmarla.net
      </li>
      <li>
        <svg viewBox="0 0 14 14" aria-hidden="true"><circle cx="7" cy="7" r="6" fill="#33b8a4"/></svg>
        @marlaprentiss
      </li>
    </ul>
    <div class="front__mark">
      <span class="front__square"></span>
      <span>form with marla</span>
    </div>
  </section>
</main>
</body>
</html>
```